Animal Eye Clinic needs a Business card

We are a new veterinary ophthalmology practice (Ridgeline Pet Vision Care) and we need a business card designed. We only see animal eyes - we are not a regular veterinary clinic. We already have a logo. We are looking for a professional, good looking business card to hand out to our clients. We are looking for something simple but professional and contemporary. Our logo is likely the only picture/graphic that needs to be on the card.
Updates

Contact Information for Business Card

Delia Vossman, BSc, DVM, MSc, DipACVO
Veterinary Ophthalmologist

Phone: 250.418.3927
Email: ridgelinepetvisioncare@mailbox-example.net
Website: ridgelinepetvisioncare-example.net
Address: 1874 Thornbury Rd
Kelowna, BC, V1X 4M9

Colors

Designer to choose colors to be used in the design.

Requirements
Must have
• Our logo (attached)

```html
<!DOCTYPE html>
<html lang="en">
<head>
<meta charset="utf-8">
<title>Ridgeline Pet Vision Care — Business Card</title>
<link rel="stylesheet" href="https://fonts.googleapis.com/css2?family=Roboto:wght@400;500;700&display=swap">
<style>
  :root {
    --teal: #1a99a8;
    --charcoal: #2d2c2c;
    --ink: #5f5f5f;
    --paper: #ffffff;
    --backdrop: #c9cbce;
  }
  * { margin: 0; padding: 0; box-sizing: border-box; }
  html, body { width: 1200px; height: 800px; overflow: hidden; }
  body {
    background: var(--backdrop);
    font-family: "Roboto", Arial, sans-serif;
    position: relative;
  }
  .card {
    position: absolute;
    width: 540px;
    height: 308px;
    border-radius: 2px;
    box-shadow: 0 6px 18px rgba(0,0,0,0.18);
    overflow: hidden;
  }

  /* Back side */
  .card-back {
    left: 560px;
    top: 70px;
    background: var(--charcoal);
  }
  .card-back .brand-mark {
    position: absolute;
    right: 56px;
    top: 74px;
    width: 160px;
    height: 160px;
    border-radius: 50%;
    background: var(--teal);
  }
  .card-back .brand-name {
    position: absolute;
    left: 40px;
    bottom: 56px;
    width: 240px;
    font-size: 25px;
    font-weight: 700;
    line-height: 1.15;
    color: var(--teal);
  }

  /* Front side */
  .card-front {
    left: 110px;
    top: 420px;
    background: var(--paper);
    padding: 34px 40px;
  }
  .brand-lockup {
    display: flex;
    align-items: center;
    gap: 12px;
  }
  .brand-lockup .brand-dot {
    width: 40px;
    height: 40px;
    border-radius: 50%;
    background: var(--teal);
    flex: none;
  }
  .brand-lockup .brand-name {
    font-size: 22px;
    font-weight: 700;
    color: var(--teal);
  }
  .person {
    margin-top: 28px;
    margin-left: 52px;
  }
  .person-name {
    font-size: 20px;
    font-weight: 700;
    color: var(--teal);
  }
  .person-name .credentials {
    font-size: 13px;
  }
  .person-title {
    font-size: 15px;
    color: var(--ink);
    margin-top: 2px;
  }
  .contact {
    list-style: none;
    margin-top: 20px;
    margin-left: 40px;
    font-size: 14.5px;
    color: var(--ink);
    line-height: 1.45;
  }
  .contact li { display: flex; align-items: center; gap: 6px; }
  .contact svg { width: 13px; height: 13px; flex: none; }
  .contact .address { padding-left: 0; margin-left: -12px; }
</style>
</head>
<body>

  <section class="card card-back" aria-label="Business card back">
    <div class="brand-mark"></div>
    <p class="brand-name">Ridgeline Pet Vision Care</p>
  </section>

  <section class="card card-front" aria-label="Business card front">
    <div class="brand-lockup">
      <span class="brand-dot"></span>
      <span class="brand-name">Ridgeline Pet Vision Care</span>
    </div>

    <div class="person">
      <p class="person-name">Delia Vossman, <span class="credentials">BSc, DVM, MSc, DipACVO</span></p>
      <p class="person-title">Veterinary Ophthalmologist</p>
    </div>

    <ul class="contact">
      <li>
        <svg viewBox="0 0 16 16" aria-hidden="true"><path fill="#1a99a8" d="M3.6 1.2 6 3.6 4.8 5.6c.9 2 2.6 3.7 4.6 4.6l2-1.2 2.4 2.4-1.6 2.4C7.4 13.4 2.6 8.6 1.2 2.8z"/></svg>
        250.418.3927
      </li>
      <li>
        <svg viewBox="0 0 16 16" aria-hidden="true"><rect x="1.5" y="3.5" width="13" height="9" fill="none" stroke="#1a99a8" stroke-width="1.4"/><path d="M1.5 3.5 8 9l6.5-5.5" fill="none" stroke="#1a99a8" stroke-width="1.4"/></svg>
        ridgelinepetvisioncare@mailbox-example.net
      </li>
      <li>
        <svg viewBox="0 0 16 16" aria-hidden="true"><g fill="none" stroke="#1a99a8" stroke-width="1.3"><circle cx="8" cy="8" r="6.3"/><ellipse cx="8" cy="8" rx="2.8" ry="6.3"/><path d="M1.7 8h12.6M2.8 4.8h10.4M2.8 11.2h10.4"/></g></svg>
        ridgelinepetvisioncare-example.net
      </li>
      <li class="address">1874 Thornbury Rd, Kelowna, BC, V1X 4M9</li>
    </ul>
  </section>

</body>
</html>
```